Need Business Card for our Real Estate Business with Sales Executive's Picture

PANTONE 484 C ( RED)

PANTONE 2766 C ( BLUE

Industry/Entity Type

Real Estate

Contact Information for Business Card

Name, Mobile, email, & picture of Person
Agency Phone, address, Web address

Requirements
Must have
• Our Logo Colours, Agent Picture,

```html
<!DOCTYPE html>
<html lang="en">
<head>
<meta charset="utf-8">
<title>Calder Real Estate – Business Card</title>
<link rel="stylesheet" href="https://fonts.googleapis.com/css2?family=Open+Sans:wght@400;600;700&display=swap">
<style>
  :root {
    --backdrop: #3a3a3a;
    --card: #1c1c1d;
    --card-edge: #262627;
    --ink: #ffffff;
    --muted: #bdbdbd;
    --deboss: #2e2e30;
    --red: #a6192e;
    --blue: #1f3a93;
    --photo-top: #5a5550;
    --photo-bottom: #1e3473;
  }
  * { margin: 0; padding: 0; box-sizing: border-box; }
  html, body { width: 799px; height: 1200px; overflow: hidden; }
  body {
    background: var(--backdrop);
    font-family: "Open Sans", sans-serif;
    color: var(--ink);
    position: relative;
  }
  .card {
    position: absolute;
    left: 60px;
    width: 680px;
    height: 389px;
    background: var(--card);
    border: 1px solid var(--card-edge);
    overflow: hidden;
  }
  .card--front { top: 130px; }
  .card--back { top: 680px; }

  /* Front */
  .front-brand {
    position: absolute;
    left: 0; right: 0; top: 130px;
    display: flex; justify-content: center; align-items: center; gap: 14px;
    font-size: 54px; font-weight: 600; letter-spacing: 8px;
    color: var(--deboss);
  }
  .front-brand__mark { width: 18px; height: 18px; background: var(--deboss); }
  .front-web {
    position: absolute;
    left: 0; right: 0; top: 318px;
    display: flex; justify-content: center; align-items: center; gap: 18px;
    font-size: 17px; letter-spacing: 0.5px;
  }
  .front-web__rule { width: 60px; height: 2px; background: var(--red); }

  /* Back */
  .brand {
    position: absolute; left: 36px; top: 36px;
    display: flex; align-items: center; gap: 10px;
    font-size: 26px; font-weight: 600; letter-spacing: 3px;
  }
  .brand__mark { width: 10px; height: 10px; background: var(--red); }
  .agent { position: absolute; left: 36px; top: 108px; }
  .agent__name { font-size: 22px; font-weight: 700; }
  .agent__title { font-size: 14px; color: var(--red); margin-top: 2px; }
  .contacts { position: absolute; left: 36px; top: 180px; list-style: none; }
  .contacts li {
    display: flex; align-items: center; gap: 10px;
    font-size: 14px; line-height: 24px;
  }
  .contacts svg { width: 13px; height: 13px; fill: var(--red); flex: none; }
  .divider { position: absolute; left: 250px; top: 296px; width: 430px; height: 1.5px; background: var(--red); }
  .agent-photo {
    position: absolute; left: 450px; top: 120px; width: 210px; height: 176px;
    background: linear-gradient(180deg, var(--photo-top), var(--photo-bottom));
  }
  .address {
    position: absolute; left: 300px; top: 302px;
    font-size: 13px; line-height: 17px;
  }
  .bands { position: absolute; left: 0; bottom: 0; width: 680px; height: 60px; }
  .web {
    position: absolute; right: 36px; bottom: 14px;
    font-size: 15px; letter-spacing: 0.3px;
  }
</style>
</head>
<body>
  <section class="card card--front" aria-label="Card front">
    <div class="front-brand"><span class="front-brand__mark"></span>CALDER</div>
    <div class="front-web">
      <span class="front-web__rule"></span>
      <span>www.calderrealestate.com</span>
      <span class="front-web__rule"></span>
    </div>
  </section>

  <section class="card card--back" aria-label="Card back">
    <div class="brand"><span class="brand__mark"></span>CALDER REAL ESTATE</div>
    <div class="agent">
      <p class="agent__name">Maren Holloway</p>
      <p class="agent__title">Managing Director</p>
    </div>
    <ul class="contacts">
      <li><svg viewBox="0 0 16 16"><rect x="3" y="1" width="10" height="14" rx="2"/></svg>555.210.4471</li>
      <li><svg viewBox="0 0 16 16"><path d="M2 6c0-3 12-3 12 0l-3 1-1-2H6L5 7zM3 8h10l1 6H2z"/></svg>555-318-2290</li>
      <li><svg viewBox="0 0 16 16"><path d="M1 3h14v10H1zM1 3l7 6 7-6"/></svg>mholloway@calderrealestate.com</li>
    </ul>
    <div class="agent-photo" role="img" aria-label="Portrait photo of the sales executive"></div>
    <div class="divider"></div>
    <p class="address">418 Ridge Ave #204,<br>Fairview, CO 80512</p>
    <svg class="bands" viewBox="0 0 680 60" aria-hidden="true">
      <polygon points="0,6 300,6 310,12 0,12" fill="#ffffff"/>
      <polygon points="0,16 316,16 340,30 0,30" fill="var(--red)"/>
      <polygon points="0,34 346,34 380,60 0,60" fill="#ffffff"/>
      <polygon points="320,14 680,14 680,60 390,60" fill="var(--blue)"/>
    </svg>
    <p class="web">www.calderrealestate.com</p>
  </section>
</body>
</html>
```